Visitenkarten/Briefpaier/Kassenkassenbelege für Juwelier
Zielgruppe
Mittelständischer Juwelier mit zwei Filialen. Klassischer Schmuck, Uhren und Modeschmuck
Aufgabenstellung
Es müssen für zwei Geschäfte Visitenkarten, Briefpapier (A4) und Kassenkassenbelege (A6) erstellt werden. Logo und Typo im Anhang. Ein Farbkonzept besteht noch nicht. Die Idee geht in Richtung Bordeaux-Rot.
Generell:
(1) Sieht erstmal nach viel Beschreibung aus, bitte nicht entmutigen lassen, sind zu 90% nur austauschbare Inhalts-/Kontaktdaten.
(2) Für meine Zwecke reicht es vollkommen aus, wenn bei den Vorschlägen zur Arbeitsersparnis erstmal nur mit einer Adresse gearbeitet wird. Wenn ich dann den zutreffenden Designvorschlag gefunden habe, können wir die zweite Adresse in dem ersten Format umsetzen. Ich denke das spart Zeit und Nerven.
(3) Bitte Angaben wie "Tel.:" oder "USt.- ID:" nicht wörtlich nehmen, es soll dabei klar sein worum es geht; wenn "Telefon" ausgeschrieben besser aussieht, bitte in der optisch ansprechenderen Form verwenden.
(4) Bei Fragen, bitte fragen!
(5) Viel Spass bei dem Projekt - Ich freu' mich auf die Vorschläge!
Visitenkarten(1):
Juwelier Brenneck GmbH
www.juwelier-brenneck-beispiel.de
Visitenkarten(2):
Visitenkarten(generell):
(1) Die einzelnen Daten können durch Hervorhebungen wie Adresse, Kontakt, Online/Internet unterteilt bzw. hervorgehoben werden.
(2) Die Visitenkarten sollen farbig gedruckt werden; geplant ist weiß als Hintergrund ist aber nicht zwingend bei einer guten anderen Idee
Briefpapier:
(1)Absender im Adressfeld für DIN-lang Briefumschläge mit Fenster:
(2)Informationen im Footer/Seitenbereich:
Juwelier Brenneck Gmb..

```html
<!DOCTYPE html>
<html lang="de">
<head>
<meta charset="utf-8">
<title>Briefpapier – Juwelier Brenneck</title>
<link href="https://fonts.googleapis.com/css2?family=Source+Sans+3:wght@400;600;700&family=Arimo&display=swap" rel="stylesheet">
<style>
  :root {
    --paper: #ffffff;
    --canvas: #ffffff;
    --band: #656565;
    --brand-grey: #8a8a8a;
    --text-dark: #4a4a4a;
    --text-mid: #7a7a7a;
    --rule: #6a6a6a;
    --mark: #9a9a9a;
    --footer-text: #ffffff;
  }
  * { margin: 0; padding: 0; box-sizing: border-box; }
  html, body { width: 1200px; height: 814px; overflow: hidden; background: var(--canvas); }
  .sheet-board { position: relative; width: 1200px; height: 814px; font-family: "Source Sans 3", sans-serif; }

  .crop { position: absolute; background: var(--mark); }
  .crop--v { width: 1px; height: 30px; }
  .crop--h { height: 1px; width: 30px; }

  .letterhead {
    position: absolute; top: 50px; width: 503px; height: 711px;
    background: var(--paper);
    box-shadow: 2px 3px 5px rgba(0,0,0,0.35);
  }
  .letterhead--a { left: 50px; }
  .letterhead--b { left: 646px; }

  .brand { position: absolute; display: flex; align-items: center; gap: 7px; }
  .brand__square { width: 9px; height: 9px; background: var(--band); }
  .brand__name { font-weight: 700; font-size: 15px; letter-spacing: 1.6px; color: var(--brand-grey); }
  .letterhead--a .brand { left: 62px; top: 65px; }
  .letterhead--b .brand { left: 28px; top: 38px; }

  .sender { position: absolute; left: 371px; top: 0; height: 138px; border-left: 1px solid var(--rule); padding: 40px 0 0 10px; }
  .sender__company { font-weight: 600; font-size: 8.6px; color: var(--text-dark); margin-bottom: 2px; }
  .sender__line { font-size: 6.8px; line-height: 10.2px; color: var(--text-mid); }
  .sender__gap { height: 10px; }

  .window { position: absolute; left: 24px; top: 122px; width: 215px; height: 84px; }
  .window__corner { position: absolute; width: 11px; height: 11px; border-color: var(--rule); border-style: solid; border-width: 0; }
  .window__corner--tl { left: 0; top: 0; border-left-width: 1px; border-top-width: 1px; }
  .window__corner--tr { right: 0; top: 0; border-right-width: 1px; border-top-width: 1px; }
  .window__corner--bl { left: 0; bottom: 0; border-left-width: 1px; border-bottom-width: 1px; }
  .window__corner--br { right: 0; bottom: 0; border-right-width: 1px; border-bottom-width: 1px; }
  .recipient { position: absolute; left: 38px; top: 12px; font-family: "Arimo", sans-serif; font-size: 9px; line-height: 14.4px; color: var(--text-dark); }

  .fold-mark { position: absolute; left: 0; width: 18px; height: 1px; background: #cccccc; }
  .fold-mark--1 { top: 253px; }
  .fold-mark--2 { top: 491px; }

  .footer-band { position: absolute; left: 0; bottom: 0; width: 100%; height: 50px; background: var(--band); color: var(--footer-text); }
  .footer-col { position: absolute; top: 0; height: 100%; display: flex; flex-direction: column; justify-content: center; }
  .footer-col--bank { left: 61px; font-size: 5.6px; line-height: 7.3px; }
  .footer-col--tax { left: 232px; font-size: 5.6px; line-height: 7.3px; }
  .footer-col--branch { left: 388px; font-size: 6.6px; line-height: 7.6px; }
  .footer-divider { position: absolute; top: 9px; width: 1px; height: 28px; background: #d8d8d8; }
  .footer-divider--1 { left: 196px; }
  .footer-divider--2 { left: 329px; }
</style>
</head>
<body>
<div class="sheet-board">
  <!-- crop marks -->
  <span class="crop crop--v" style="left:50px;top:5px"></span>
  <span class="crop crop--v" style="left:552px;top:5px"></span>
  <span class="crop crop--v" style="left:646px;top:5px"></span>
  <span class="crop crop--v" style="left:1148px;top:5px"></span>
  <span class="crop crop--v" style="left:50px;top:776px"></span>
  <span class="crop crop--v" style="left:552px;top:776px"></span>
  <span class="crop crop--v" style="left:646px;top:776px"></span>
  <span class="crop crop--v" style="left:1148px;top:776px"></span>
  <span class="crop crop--h" style="left:5px;top:50px"></span>
  <span class="crop crop--h" style="left:568px;top:50px"></span>
  <span class="crop crop--h" style="left:600px;top:50px"></span>
  <span class="crop crop--h" style="left:1163px;top:50px"></span>
  <span class="crop crop--h" style="left:5px;top:761px"></span>
  <span class="crop crop--h" style="left:568px;top:761px"></span>
  <span class="crop crop--h" style="left:600px;top:761px"></span>
  <span class="crop crop--h" style="left:1163px;top:761px"></span>

  <section class="letterhead letterhead--a">
    <div class="brand"><span class="brand__square"></span><span class="brand__name">JUWELIER BRENNECK</span></div>
    <div class="sender">
      <p class="sender__company">Juwelier Brenneck GmbH</p>
      <p class="sender__line">Lindenallee 14</p>
      <p class="sender__line">45100 Musterstadt</p>
      <div class="sender__gap"></div>
      <p class="sender__line">Tel.: 0200-123450</p>
      <p class="sender__line">Fax: 0200-123459</p>
      <p class="sender__line">info@juwelier-brenneck-beispiel.de</p>
      <p class="sender__line">www.juwelier-brenneck-beispiel.de</p>
    </div>
    <div class="window">
      <span class="window__corner window__corner--tl"></span><span class="window__corner window__corner--tr"></span>
      <span class="window__corner window__corner--bl"></span><span class="window__corner window__corner--br"></span>
      <p class="recipient">Marie Beispiel<br>Am Musterweg 8<br>53700 Beispielort<br>SCHWEIZ</p>
    </div>
    <span class="fold-mark fold-mark--1"></span><span class="fold-mark fold-mark--2"></span>
    <footer class="footer-band">
      <div class="footer-col footer-col--bank"><span>Bankverbindung:</span><span>Beispielbank AG Musterstadt</span><span>IBAN: DE00 1234 5678 9012 3456 78</span><span>BIC: BSPB DE 1X</span></div>
      <span class="footer-divider footer-divider--1"></span>
      <div class="footer-col footer-col--tax"><span>Steuernummer:</span><span>100/0000/0000</span><span>USt.- ID: DE 000000000</span></div>
      <span class="footer-divider footer-divider--2"></span>
      <div class="footer-col footer-col--branch"><span>Filiale:</span><span>Gartenstraße 3</span><span>45500 Nebenstadt</span></div>
    </footer>
  </section>

  <section class="letterhead letterhead--b">
    <div class="brand"><span class="brand__square"></span><span class="brand__name">JUWELIER BRENNECK</span></div>
    <div class="sender">
      <p class="sender__company">Juwelier Brenneck GmbH</p>
      <p class="sender__line">Lindenallee 14</p>
      <p class="sender__line">45100 Musterstadt</p>
      <div class="sender__gap"></div>
      <p class="sender__line">Tel.: 0200-123450</p>
      <p class="sender__line">Fax: 0200-123459</p>
      <p class="sender__line">info@juwelier-brenneck-beispiel.de</p>
      <p class="sender__line">www.juwelier-brenneck-beispiel.de</p>
    </div>
    <div class="window">
      <span class="window__corner window__corner--tl"></span><span class="window__corner window__corner--tr"></span>
      <span class="window__corner window__corner--bl"></span><span class="window__corner window__corner--br"></span>
      <p class="recipient">Marie Beispiel<br>Am Musterweg 8<br>53700 Beispielort<br>SCHWEIZ</p>
    </div>
    <span class="fold-mark fold-mark--1"></span><span class="fold-mark fold-mark--2"></span>
    <footer class="footer-band">
      <div class="footer-col footer-col--bank"><span>Bankverbindung:</span><span>Beispielbank AG Musterstadt</span><span>IBAN: DE00 1234 5678 9012 3456 78</span><span>BIC: BSPB DE 1X</span></div>
      <span class="footer-divider footer-divider--1"></span>
      <div class="footer-col footer-col--tax"><span>Steuernummer:</span><span>100/0000/0000</span><span>USt.- ID: DE 000000000</span></div>
      <span class="footer-divider footer-divider--2"></span>
      <div class="footer-col footer-col--branch"><span>Filiale:</span><span>Gartenstraße 3</span><span>45500 Nebenstadt</span></div>
    </footer>
  </section>
</div>
</body>
</html>
```